Automotive Accessories Business Card

Design a business template that match our new logo design and our industry.

https://www.qelmotorgear.com/

Target Market(s)

Aftermarket auto parts and accessories

Industry/Entity Type

automotive

Contact Information for Business Card

company logo

Font styles to use
Serif
Sans Serif

Colors
EB3D1F
EC4F4E
F09395
F8D3D4
FCEDEE

```html
<!DOCTYPE html>
<html lang="en">
<head>
<meta charset="utf-8">
<title>QEL Motor Gear – Business Card</title>
<link href="https://fonts.googleapis.com/css2?family=Montserrat:wght@400;500;700;800&display=swap" rel="stylesheet">
<style>
  :root {
    --bg: #e9e9e9;
    --paper: #ffffff;
    --ink: #3a3a3c;
    --ink-soft: #555558;
    --red: #d8212b;
    --charcoal: #2b2b2d;
    --charcoal-light: #6b6b6e;
    --rule: #6a6a6a;
  }
  * { box-sizing: border-box; margin: 0; padding: 0; }
  html, body { width: 1200px; height: 802px; overflow: hidden; }
  body {
    background: var(--bg);
    font-family: "Montserrat", Arial, sans-serif;
    color: var(--ink);
    position: relative;
  }
  .card {
    position: absolute;
    top: 250px;
    width: 520px;
    height: 297px;
    border-bottom: 4px solid var(--red);
    box-shadow: 0 6px 18px rgba(0,0,0,0.12);
  }
  .card--front { left: 50px; background: var(--paper); }
  .card--back { left: 630px; background: var(--charcoal); overflow: hidden; }

  .brand {
    position: absolute;
    left: 40px;
    top: 44px;
    display: flex;
    align-items: center;
    gap: 10px;
    font-weight: 800;
    font-size: 26px;
    letter-spacing: 1px;
    color: var(--charcoal);
  }
  .brand__mark { width: 14px; height: 14px; background: var(--red); }

  .address {
    position: absolute;
    right: 36px;
    top: 34px;
    text-align: right;
    font-size: 12px;
    line-height: 1.45;
    color: var(--ink-soft);
  }

  .person { position: absolute; left: 40px; top: 140px; }
  .person__name {
    font-weight: 800;
    font-size: 19px;
    letter-spacing: 1.5px;
    color: var(--red);
    text-transform: uppercase;
  }
  .person__role { font-size: 13px; color: var(--ink-soft); margin-top: 2px; }

  .divider {
    position: absolute;
    left: 40px; right: 36px; top: 196px;
    height: 1px;
    background: var(--rule);
  }

  .contacts {
    position: absolute;
    left: 40px;
    top: 208px;
    list-style: none;
    font-size: 13px;
    line-height: 1.55;
    color: var(--ink-soft);
  }
  .contacts li { display: flex; align-items: center; gap: 8px; }
  .contacts svg { width: 11px; height: 11px; fill: var(--red); flex: none; }

  .back__pattern {
    position: absolute; inset: 0;
    background: linear-gradient(120deg, #1f1f21 0%, #2f2f31 45%, #6c6c6f 80%, #8a8a8d 100%);
  }
  .back__brand {
    position: absolute;
    left: 50%; top: 50%;
    transform: translate(-50%, -50%);
    display: flex;
    align-items: center;
    gap: 9px;
    font-weight: 800;
    font-size: 22px;
    letter-spacing: 1px;
    color: #ffffff;
    white-space: nowrap;
  }
  .back__brand .brand__mark { width: 12px; height: 12px; }
</style>
</head>
<body>
  <section class="card card--front" aria-label="Business card front">
    <div class="brand"><span class="brand__mark"></span>QEL MOTOR GEAR</div>
    <address class="address">
      248 W. Harbor Ave.<br>Suite B<br>Riverton, CA 92880
    </address>
    <div class="person">
      <p class="person__name">Daniel Reyes</p>
      <p class="person__role">Manager</p>
    </div>
    <div class="divider"></div>
    <ul class="contacts">
      <li>
        <svg viewBox="0 0 24 24"><path d="M6.6 10.8a15 15 0 0 0 6.6 6.6l2.2-2.2a1 1 0 0 1 1-.25 11.4 11.4 0 0 0 3.6.57 1 1 0 0 1 1 1V20a1 1 0 0 1-1 1A17 17 0 0 1 3 4a1 1 0 0 1 1-1h3.5a1 1 0 0 1 1 1c0 1.25.2 2.45.57 3.57a1 1 0 0 1-.25 1z"/></svg>
        1-866-555-0148
      </li>
      <li>
        <svg viewBox="0 0 24 24"><path d="M2 5h20v14H2z M2 5l10 8 10-8" /></svg>
        sales@qelmotorgear.com
      </li>
      <li>
        <svg viewBox="0 0 24 24"><circle cx="12" cy="12" r="10"/></svg>
        www.qelmotorgear.com
      </li>
    </ul>
  </section>

  <section class="card card--back" aria-label="Business card back">
    <div class="back__pattern" role="img" aria-label="Repeating tone-on-tone brand pattern in dark to light grey"></div>
    <div class="back__brand"><span class="brand__mark"></span>QEL MOTOR GEAR</div>
  </section>
</body>
</html>
```